Realtor branding business card

modern, simple and self branding. Broker office logo needs to be used but not emphasized. Looking to brand myself

Target Market(s)

buyers, sellers and investors

Industry/Entity Type

Realtor

Contact Information for Business Card

Sample of my current business card on file

Requirements
Must have
• my website - tobiasmerrowkl.com
• Realtor logo
• Fair housing logo
Nice to have
• Colors from office logo but not a must
Should not have
• Do not want headshot

```html
<!DOCTYPE html>
<html lang="en">
<head>
<meta charset="utf-8">
<title>Tobias Merrow – Realtor Business Card</title>
<link href="https://fonts.googleapis.com/css2?family=Arimo:wght@400;700&display=swap" rel="stylesheet">
<style>
  :root {
    --backdrop: #2b2b2b;
    --card: #f7f7f9;
    --navy: #2a2580;
    --red: #d8231f;
    --ink: #1c1c2a;
  }
  html, body {
    margin: 0;
    padding: 0;
    width: 1200px;
    height: 997px;
    overflow: hidden;
    background: var(--backdrop);
    font-family: "Arimo", Arial, sans-serif;
  }
  .card {
    position: absolute;
    width: 540px;
    height: 310px;
    background: var(--card);
    border-radius: 16px;
    overflow: hidden;
    box-sizing: border-box;
  }
  .card::after {
    content: "";
    position: absolute;
    left: 0; right: 0; bottom: 0;
    height: 10px;
    background: var(--navy);
  }
  .card-front { left: 70px; top: 120px; }
  .card-back { left: 590px; top: 500px; }

  .brand {
    display: flex;
    align-items: center;
    gap: 12px;
    color: var(--navy);
    font-weight: 700;
    line-height: 1;
    white-space: nowrap;
  }
  .brand-mark {
    background: var(--red);
    flex: none;
    border-radius: 50%;
  }
  .card-front .brand {
    position: absolute;
    left: 0; right: 0; top: 132px;
    justify-content: center;
    font-size: 36px;
  }
  .card-front .brand-mark { width: 20px; height: 20px; }

  .card-back .brand {
    position: absolute;
    left: 150px; top: 36px;
    font-size: 26px;
  }
  .card-back .brand-mark { width: 14px; height: 14px; }

  .rule {
    position: absolute;
    left: 150px; right: 40px; top: 96px;
    height: 2px;
    background: var(--navy);
  }
  .agent {
    position: absolute;
    left: 40px; top: 150px;
  }
  .agent-name {
    margin: 0;
    color: var(--red);
    font-size: 17px;
    font-weight: 700;
    letter-spacing: 0.3px;
  }
  .agent-title {
    margin: 2px 0 0;
    color: var(--ink);
    font-size: 14px;
  }
  .contact {
    list-style: none;
    margin: 10px 0 0;
    padding: 0;
    color: var(--ink);
    font-size: 14px;
    line-height: 1.25;
  }
  .contact li {
    display: flex;
    align-items: flex-start;
    gap: 10px;
    margin-bottom: 3px;
  }
  .contact svg { flex: none; margin-top: 1px; }
  .website {
    position: absolute;
    right: 40px; top: 200px;
    color: var(--navy);
    font-size: 15px;
    font-weight: 700;
  }
  .badges {
    position: absolute;
    right: 40px; top: 236px;
    display: flex;
    gap: 10px;
  }
  .badge {
    width: 32px;
    height: 32px;
    background: var(--navy);
  }
  .badge-realtor { border-radius: 4px; }
  .badge-fair-housing { border-radius: 50%; }
</style>
</head>
<body>

<section class="card card-front">
  <div class="brand"><span class="brand-mark"></span>Northvale Realty Group</div>
</section>

<section class="card card-back">
  <div class="brand"><span class="brand-mark"></span>Northvale Realty Group</div>
  <div class="rule"></div>

  <div class="agent">
    <h1 class="agent-name">TOBIAS MERROW, PA</h1>
    <p class="agent-title">Realtor</p>
    <ul class="contact">
      <li>
        <svg width="14" height="14" viewBox="0 0 14 14"><circle cx="7" cy="7" r="7" fill="var(--navy)"/><path d="M4.5 3.5l1.5 0.2 0.5 1.8-0.9 0.7a5 5 0 0 0 2.2 2.2l0.7-0.9 1.8 0.5 0.2 1.5c-3.5 0.5-6.7-2.7-6.2-6z" fill="#fff"/></svg>
        <span>(407) 555-0148</span>
      </li>
      <li>
        <svg width="14" height="14" viewBox="0 0 14 14"><circle cx="7" cy="7" r="7" fill="var(--navy)"/><rect x="4" y="5" width="6" height="4" fill="#fff"/><rect x="5" y="3.5" width="4" height="2" fill="#fff"/></svg>
        <span>(407) 555-0192</span>
      </li>
      <li>
        <svg width="14" height="14" viewBox="0 0 14 14"><circle cx="7" cy="7" r="7" fill="var(--navy)"/><rect x="3.5" y="4.5" width="7" height="5" fill="#fff"/><path d="M3.5 4.5l3.5 3 3.5-3" stroke="var(--navy)" stroke-width="0.8" fill="none"/></svg>
        <span>merrowrealty@mailbox.com</span>
      </li>
      <li>
        <svg width="14" height="14" viewBox="0 0 14 14"><circle cx="7" cy="7" r="7" fill="var(--navy)"/><path d="M7 3a2.4 2.4 0 0 1 2.4 2.4C9.4 7.2 7 10.5 7 10.5S4.6 7.2 4.6 5.4A2.4 2.4 0 0 1 7 3z" fill="#fff"/></svg>
        <span>481 Larkspur Avenue #310,<br>Cedar Glen FL 32790</span>
      </li>
    </ul>
  </div>

  <div class="website">www.tobiasmerrowkl.com</div>

  <div class="badges">
    <div class="badge badge-realtor" role="img" aria-label="Realtor association badge"></div>
    <div class="badge badge-fair-housing" role="img" aria-label="Equal housing opportunity badge"></div>
  </div>
</section>

</body>
</html>
```